Animal Eye Clinic needs a Business card

We are a new veterinary ophthalmology practice (Ridgeline Pet Vision Care) and we need a business card designed. We only see animal eyes - we are not a regular veterinary clinic. We already have a logo. We are looking for a professional, good looking business card to hand out to our clients. We are looking for something simple but professional and contemporary. Our logo is likely the only picture/graphic that needs to be on the card.
Updates

Contact Information for Business Card

Delia Vossman, BSc, DVM, MSc, DipACVO
Veterinary Ophthalmologist

Phone: 250.418.3927
Email: ridgelinepetvisioncare@mailbox-example.net
Website: ridgelinepetvisioncare-example.net
Address: 1874 Thornbury Rd
Kelowna, BC, V1X 4M9

Colors

Designer to choose colors to be used in the design.

Requirements
Must have
• Our logo (attached)

```html
<!DOCTYPE html>
<html lang="en">
<head>
<meta charset="utf-8">
<title>Ridgeline Pet Vision Care – Business Card</title>
<link rel="stylesheet" href="https://fonts.googleapis.com/css2?family=Source+Sans+3:wght@400;600;700&display=swap">
<style>
  :root {
    --teal: #0797a8;
    --grey: #7a7a7a;
    --ink: #2b2b2b;
    --muted: #8a8a8a;
    --white: #ffffff;
    --backdrop: #ececec;
  }
  * { box-sizing: border-box; margin: 0; padding: 0; }
  html, body { width: 1200px; height: 1200px; overflow: hidden; }
  body {
    background: var(--backdrop);
    font-family: "Source Sans 3", sans-serif;
    display: flex;
    flex-direction: column;
    align-items: center;
    justify-content: center;
    gap: 90px;
  }
  .card {
    position: relative;
    width: 760px;
    height: 430px;
    overflow: hidden;
  }
  .card--front { background: var(--white); }
  .card--back { background: var(--teal); color: var(--white); }

  .animal-art {
    position: absolute;
    left: 0;
    top: 0;
    width: 296px;
    height: 430px;
    border-radius: 0 60% 60% 0 / 0 55% 45% 0;
  }
  .card--front .animal-art { background: var(--grey); }
  .card--back .animal-art { background: var(--white); }

  .brand {
    position: absolute;
    left: 300px;
    top: 172px;
    display: flex;
    align-items: center;
    gap: 14px;
  }
  .brand__dot {
    width: 60px;
    height: 60px;
    border-radius: 50%;
    background: var(--teal);
    flex: none;
  }
  .card--back .brand__dot { background: var(--white); }
  .brand__name {
    font-weight: 700;
    font-size: 26px;
    line-height: 1.05;
    text-transform: uppercase;
    letter-spacing: 0.5px;
    color: var(--teal);
  }
  .card--back .brand__name { color: var(--white); }

  .holder {
    position: absolute;
    left: 404px;
    top: 362px;
  }
  .holder__name { font-size: 17px; color: var(--ink); line-height: 1.3; }
  .holder__role { font-size: 15px; color: var(--muted); line-height: 1.3; }

  .contact {
    position: absolute;
    left: 404px;
    top: 312px;
    list-style: none;
    font-size: 15.5px;
    line-height: 25px;
  }
  .contact li { display: flex; align-items: center; gap: 8px; }
  .contact svg { width: 15px; height: 15px; flex: none; fill: var(--white); }
</style>
</head>
<body>

  <section class="card card--front" aria-label="Business card front">
    <div class="animal-art" role="img" aria-label="Silhouettes of a horse head and a cat in grey"></div>
    <div class="brand">
      <span class="brand__dot"></span>
      <span class="brand__name">Ridgeline<br>Pet Vision Care</span>
    </div>
    <div class="holder">
      <p class="holder__name">Delia Vossman, BSc, DVM, MSc, DipACVO</p>
      <p class="holder__role">Veterinary Ophthalmologist</p>
    </div>
  </section>

  <section class="card card--back" aria-label="Business card back">
    <div class="animal-art" role="img" aria-label="Silhouettes of a horse head and a cat in white"></div>
    <div class="brand">
      <span class="brand__dot"></span>
      <span class="brand__name">Ridgeline<br>Pet Vision Care</span>
    </div>
    <ul class="contact">
      <li>
        <svg viewBox="0 0 16 16" aria-hidden="true"><path d="M3.5 1.5l2.5 0 1 3.5-1.6 1.2a8 8 0 0 0 4.4 4.4L11 9l3.5 1v2.5a1.5 1.5 0 0 1-1.6 1.5A12 12 0 0 1 2 3.1 1.5 1.5 0 0 1 3.5 1.5z"/></svg>
        250.418.3927
      </li>
      <li>
        <svg viewBox="0 0 16 16" aria-hidden="true"><path d="M1 3.5h14v1L8 9 1 4.5z"/><path d="M1 6l7 4.5L15 6v7H1z"/></svg>
        ridgelinepetvisioncare@mailbox-example.net
      </li>
      <li>
        <svg viewBox="0 0 16 16" aria-hidden="true"><path d="M8 1a7 7 0 1 0 0 14A7 7 0 0 0 8 1zm0 1.5c.8 0 1.8 1.7 2 4.5H6c.2-2.8 1.2-4.5 2-4.5zM2.6 7A5.5 5.5 0 0 1 5.4 3 10 10 0 0 0 4.5 7zm0 2h1.9a10 10 0 0 0 .9 4A5.5 5.5 0 0 1 2.6 9zM8 13.5c-.8 0-1.8-1.7-2-4.5h4c-.2 2.8-1.2 4.5-2 4.5zM10.6 13a10 10 0 0 0 .9-4h1.9a5.5 5.5 0 0 1-2.8 4zm.9-6a10 10 0 0 0-.9-4 5.5 5.5 0 0 1 2.8 4z"/></svg>
        ridgelinepetvisioncare-example.net
      </li>
      <li>
        <svg viewBox="0 0 16 16" aria-hidden="true"><path d="M8 1a5 5 0 0 0-5 5c0 3.8 5 9 5 9s5-5.2 5-9a5 5 0 0 0-5-5zm0 7a2 2 0 1 1 0-4 2 2 0 0 1 0 4z"/></svg>
        1874 Thornbury Rd Kelowna, BC, V1X 4M9
      </li>
    </ul>
  </section>

</body>
</html>
```